Buch-/E-Book-Cover für einen historischen Roman
Zielgruppe
Buchautor historische Romane, Zielgruppe 60 % weiblich, 35 +
Aufgabenstellung
Die Farbgebung und Schrifttype sollen sich an die ersten 4 Bänder der Serie 'Das Findelkind und der Abt' https://www.buchkontor.de/Findelkind-Abt-Historischer-Roman-ebook/dp/Q417K2RMWX, anpassen, da der Buchtitel 'Die Gräfin und der Falschspieler' der 5 Band dieser Serie ist. Die Grafik kann aber etwas abweichen, im Mittelpunkt des Romans steht das Verschwinden eines Siegelrings. Der sollte abgebildet sein, in dem Roman werden Frau und kleiner Sohn des Herzogs entführt und in einem alten Herrenhaus im englischen Marschland wiedergefunden.

```html
<!DOCTYPE html>
<html lang="de">
<head>
<meta charset="utf-8">
<title>Die Gräfin und der Falschspieler – Buch fünf</title>
<link rel="stylesheet" href="https://fonts.googleapis.com/css2?family=Cinzel:wght@400;700;900&family=IM+Fell+English:ital@1&display=swap">
<style>
  :root {
    --parchment-light: #f3ecc6;
    --parchment-mid: #d9c48f;
    --parchment-dark: #7d5a2c;
    --author-red: #b0141b;
    --ink: #111008;
    --ring-gold: #c9936a;
    --ring-stone: #5d5a4c;
    --land-green: #4b5032;
    --land-sky: #b8ad82;
  }
  html, body {
    margin: 0;
    padding: 0;
    overflow: hidden;
    background: #ffffff;
  }
  .cover {
    position: relative;
    width: 750px;
    height: 1200px;
    overflow: hidden;
    background:
      radial-gradient(ellipse 70% 55% at 50% 55%, var(--parchment-light) 0%, var(--parchment-mid) 60%, var(--parchment-dark) 115%);
    font-family: "Cinzel", serif;
    color: var(--ink);
    text-align: center;
  }
  .author {
    position: absolute;
    top: 78px;
    left: 0;
    width: 100%;
    margin: 0;
    font-weight: 400;
    font-size: 74px;
    letter-spacing: 0;
    line-height: 1;
    color: var(--author-red);
  }
  .signet-ring {
    position: absolute;
    left: 326px;
    top: 190px;
    width: 125px;
    height: 145px;
    border-radius: 50% 50% 45% 45%;
    background: radial-gradient(circle at 50% 32%, var(--ring-stone) 0%, var(--ring-stone) 32%, var(--ring-gold) 40%, #e6c6a4 75%, #b98560 100%);
  }
  .title {
    position: absolute;
    top: 372px;
    left: 0;
    width: 100%;
    margin: 0;
    font-weight: 400;
  }
  .title span { display: block; }
  .title .connector {
    font-family: "IM Fell English", serif;
    font-style: italic;
    font-size: 70px;
    line-height: 1;
  }
  .title .connector-top { margin-left: 20px; }
  .title .main-word {
    font-family: "Cinzel", serif;
    font-weight: 700;
    font-size: 124px;
    line-height: 1;
    margin-top: 6px;
  }
  .title .connector-mid { margin: 2px 0 6px 10px; }
  .title .second-word {
    font-family: "Cinzel", serif;
    font-weight: 700;
    font-size: 54px;
    line-height: 1;
    letter-spacing: 0;
  }
  .flourish {
    position: absolute;
    left: 322px;
    top: 758px;
    width: 118px;
    height: 44px;
    border-radius: 22px;
    background: linear-gradient(90deg, rgba(17,16,8,0.18), rgba(17,16,8,0.32), rgba(17,16,8,0.18));
  }
  .volume {
    position: absolute;
    top: 852px;
    left: 0;
    width: 100%;
    margin: 0;
    font-weight: 700;
    font-size: 23px;
    letter-spacing: 0.5px;
  }
  .manor-landscape {
    position: absolute;
    left: 0;
    bottom: 0;
    width: 750px;
    height: 220px;
    background: linear-gradient(180deg, rgba(184,173,130,0) 0%, var(--land-sky) 25%, #5d6140 50%, var(--land-green) 70%, #3b3d28 100%);
  }
</style>
</head>
<body>
<main class="cover">
  <p class="author">JONAS WERBECK</p>
  <div class="signet-ring" role="img" aria-label="Goldener Siegelring mit Wappen und Steinbesatz"></div>
  <h1 class="title">
    <span class="connector connector-top">Die</span>
    <span class="main-word">GRÄFIN</span>
    <span class="connector connector-mid">und der</span>
    <span class="second-word">FALSCHSPIELER</span>
  </h1>
  <div class="flourish" role="img" aria-label="Geschwungenes Zierornament"></div>
  <p class="volume">BUCH FÜNF</p>
  <div class="manor-landscape" role="img" aria-label="Altes englisches Herrenhaus hinter Bäumen und Wiese im Dunst"></div>
</main>
</body>
</html>
```